FinTech company looking to revamp and expand client-facing interface for our financial models

Pellworth Engines currently has a very simple website that allows clients to interact with our financial models. We are looking to completely redesign the current site and add several extra pages to provide extra functionality. We want the design to have a modern, slick feel, that will work on both a desktop or a tablet. It should be straightforward for clients to move between different pages at any time, and clear from the layout how to interact with the more advanced features. We have included screenshots of existing pages in the attached design brief, as well as sketches of the functionality required by the new pages, but can't provide a direct link to the current site.
Target Market(s)
Professional investors that will be paying to access the interface
Industry/Entity Type
Finance
Number of Pages Required
4 page
Colors
Designer to choose colors to be used in the design.
Look and feel
Each slider illustrates characteristics of the customer's brand and the style your logo design should communicate.

```html
<!DOCTYPE html>
<html lang="en">
<head>
<meta charset="utf-8">
<title>Veldra – Factor Selection</title>
<link rel="stylesheet" href="https://fonts.googleapis.com/css2?family=Open+Sans:wght@400;600;700&display=swap">
<style>
:root{
  --teal:#006a66;
  --teal-bright:#24a694;
  --ink:#1a1a1a;
  --mint:#e2f2ee;
  --badge:#9a9a9a;
  --page:#f6f6f6;
  --white:#ffffff;
  --rule:#e4e4e4;
  --text:#222222;
}
*{box-sizing:border-box;margin:0;padding:0}
html,body{width:1135px;height:1200px;overflow:hidden}
body{font-family:"Open Sans",Arial,sans-serif;color:var(--text);
  background:linear-gradient(#e6e6e6 52px,#efefef 140px,var(--page) 300px);position:relative}
.topbar{position:absolute;left:0;top:0;width:1135px;height:52px;background:var(--white);
  box-shadow:0 3px 10px rgba(0,0,0,.12)}
.brand{position:absolute;left:63px;top:15px;font-weight:700;font-size:17px;color:var(--ink)}
.range{position:absolute;top:0;height:52px;line-height:52px;text-align:center;font-weight:700;font-size:13px;border-right:1px solid #eee}
.range.active{background:var(--teal-bright);color:var(--white)}
.nav-item{position:absolute;top:0;height:52px;display:flex;align-items:center;justify-content:center;gap:7px;
  font-weight:700;font-size:11.5px;border-left:1px solid #eee;color:var(--ink)}
.nav-item svg{width:20px;height:20px}
.badge{position:absolute;left:61px;width:284px;height:35px;background:var(--badge);color:var(--white);
  border-radius:3px;font-weight:600;font-size:14.5px;line-height:35px;text-align:center;letter-spacing:.2px}
.card{position:absolute;left:61px;width:1013px;background:var(--white);border-radius:4px;
  box-shadow:0 2px 8px rgba(0,0,0,.1);overflow:hidden}
.stats{top:135px;border-collapse:collapse}
.stats table{width:100%;border-collapse:collapse;font-size:15px}
.stats th{height:61px;background:var(--teal);color:var(--white);font-weight:700;font-size:15px;width:157px;border-left:1px solid #0a5956}
.stats th.id{background:var(--ink);width:384px;border-left:none}
.stats td{height:59px;text-align:center;border-left:1px solid #eee}
.stats td:first-child{border-left:none}
.stats tr.alt td{background:var(--mint)}
.pool{top:471px}
.pool table{width:100%;border-collapse:collapse;font-size:15px}
.pool td{height:61.2px;text-align:center;width:20%;border-left:1px solid #eee}
.pool td:first-child{border-left:none}
.pool tr.alt td{background:var(--mint)}
.toggle{position:absolute;left:1047px;top:427px;width:28px;height:28px}
.chart-card{top:760px;height:370px}
.chart-head{position:absolute;left:0;top:0;width:100%;height:74px;background:#efefef}
.ctab{position:absolute;top:43px;width:79px;height:31px;background:var(--white);text-align:center;line-height:33px;
  font-size:15px;font-weight:600;border-radius:3px 3px 0 0}
.ctab.active{top:35px;height:39px;background:#c6c6c6;line-height:40px;color:#444}
.plot{position:absolute;left:0;top:74px}
</style>
</head>
<body>
<header class="topbar">
  <div class="brand">VELDRA</div>
  <div class="range active" style="left:170px;width:79px">250D</div>
  <div class="range" style="left:249px;width:78px">83D</div>
  <div class="range" style="left:327px;width:79px">42D</div>
  <div class="nav-item" style="left:525px;width:122px">
    <svg viewBox="0 0 20 20"><path d="M2 10 10 3l8 7M4.5 8v9h4v-5h3v5h4V8" fill="none" stroke="#1a1a1a" stroke-width="2"/></svg>MODELS</div>
  <div class="nav-item" style="left:647px;width:154px">
    <svg viewBox="0 0 20 20" fill="#1a1a1a"><circle cx="10" cy="10" r="3"/><circle cx="10" cy="3" r="1.5"/><circle cx="10" cy="17" r="1.5"/><circle cx="3" cy="10" r="1.5"/><circle cx="17" cy="10" r="1.5"/><circle cx="5" cy="5" r="1.5"/><circle cx="15" cy="5" r="1.5"/><circle cx="5" cy="15" r="1.5"/><circle cx="15" cy="15" r="1.5"/></svg>SENSITIVITIES</div>
  <div class="nav-item" style="left:801px;width:140px">
    <svg viewBox="0 0 20 20" fill="none" stroke="#1a1a1a" stroke-width="1.6"><circle cx="5.5" cy="5.5" r="3.5"/><circle cx="14.5" cy="5.5" r="3.5"/><circle cx="5.5" cy="14.5" r="3.5"/><circle cx="14.5" cy="14.5" r="3.5"/></svg>PORTFOLIO</div>
  <div class="nav-item" style="left:941px;width:133px;border-right:1px solid #eee">
    <svg viewBox="0 0 20 20" fill="none" stroke="#1a1a1a" stroke-width="1.6"><rect x="1.5" y="2.5" width="17" height="15"/><path d="M4 14l4-5 3 3 5-6"/></svg>BACKTEST</div>
</header>

<div class="badge" style="top:87px">Number of Selected Factors : 3</div>
<section class="card stats">
  <table>
    <tr><th class="id">ID &#8964;</th><th>Stat 1</th><th>Stat 2</th><th>Stat 3</th><th>Stat 4</th></tr>
    <tr><td>Factor 1</td><td>-1.4</td><td>0.094</td><td>6.1</td><td>100</td></tr>
    <tr class="alt"><td>Factor 2</td><td>2.8</td><td>0.085</td><td>3.1</td><td>0.7</td></tr>
    <tr><td>Factor 3</td><td>-3.7</td><td>2.7</td><td>-7.2</td><td>100</td></tr>
  </table>
</section>

<div class="badge" style="top:423px">Unselected Factors</div>
<svg class="toggle" viewBox="0 0 28 28"><circle cx="14" cy="14" r="13" fill="#fff" stroke="#bbb"/><circle cx="14" cy="14" r="10.5" fill="#333"/><path d="M9 16l5-5 5 5" fill="none" stroke="#fff" stroke-width="2"/></svg>
<section class="card pool">
  <table>
    <tr class="alt"><td>Factor</td><td>Factor</td><td>Factor</td><td>Factor</td><td>Factor</td></tr>
    <tr><td>Factor</td><td>Factor</td><td>Factor</td><td>Factor</td><td>Factor</td></tr>
    <tr class="alt"><td>Factor</td><td>Factor</td><td>Factor</td><td>Factor</td><td>Factor</td></tr>
    <tr><td>Factor</td><td>Factor</td><td>Factor</td><td>Factor</td><td>Factor</td></tr>
  </table>
</section>

<section class="card chart-card">
  <div class="chart-head">
    <div class="ctab" style="left:48px">#1</div>
    <div class="ctab" style="left:131px">#2</div>
    <div class="ctab" style="left:214px">#3</div>
    <div class="ctab active" style="left:297px">#4</div>
  </div>
  <svg class="plot" width="1013" height="296" viewBox="70 955 1160 339" font-family="Open Sans, Arial, sans-serif">
    <g stroke="#eee" stroke-width="1">
      <path d="M150 1018H1077M150 1055H1077M150 1092H1077M150 1130H1077M150 1168H1077"/>
      <path d="M182 1003V1205M325 1003V1205M465 1003V1205M605 1003V1205M742 1003V1205M882 1003V1205M1022 1003V1205"/>
    </g>
    <path d="M150 1205H1077" stroke="#888" stroke-width="1.2"/>
    <g font-size="11" fill="#555" text-anchor="end">
      <text x="150" y="1022">100</text><text x="150" y="1059">80</text><text x="150" y="1096">60</text>
      <text x="150" y="1134">40</text><text x="150" y="1172">20</text><text x="150" y="1209">0</text>
    </g>
    <g font-size="11" fill="#555" text-anchor="middle">
      <text x="182" y="1230">Jul 2018</text><text x="325" y="1230">Sep 2018</text><text x="465" y="1230">Nov 2018</text>
      <text x="605" y="1230">Jan 2019</text><text x="742" y="1230">Mar 2019</text><text x="882" y="1230">May 2019</text><text x="1022" y="1230">Jul 2019</text>
    </g>
    <path fill="none" stroke="#b9b83a" stroke-width="7" stroke-linecap="round" d="M202 1018h0M209 1018h0M216 1018h0M223 1018h0M230 1018h0M237 1018h0M244 1018h0M251 1018h0M258 1018h0M265 1018h0M272 1018h0M279 1018h0M286 1025h0M290 1030h0M295 1020h0M300 1026h0M305 1022h0M310 1025h0M316 1020h0M320 1027h0M326 1024h0M333 1030h0M337 1083h0M340 1113h0M345 1135h0M350 1100h0M355 1115h0M360 1133h0M365 1120h0M370 1110h0M375 1125h0M382 1078h0M385 1083h0M388 1058h0M393 1048h0M398 1045h0M400 1022h0M407 1025h0M410 1093h0M413 1082h0M418 1100h0M422 1110h0M428 1105h0M430 1100h0M436 1175h0M440 1165h0M445 1190h0M450 1155h0M455 1180h0M458 1165h0M462 1150h0M466 1198h0M470 1195h0M475 1190h0M480 1200h0M485 1185h0M490 1180h0M495 1160h0M500 1170h0M505 1150h0M510 1140h0M515 1155h0M520 1145h0M525 1140h0M528 1105h0M532 1092h0M537 1095h0M540 1020h0M545 1025h0M550 1020h0M556 1018h0M560 1025h0M566 1030h0M573 1040h0M577 1192h0M581 1195h0M591 1190h0M596 1195h0M601 1185h0M606 1188h0M611 1180h0M616 1182h0M621 1178h0M626 1190h0M631 1185h0M636 1192h0M640 1180h0M645 1155h0M650 1152h0M655 1080h0M660 1135h0M667 1080h0M668 1118h0M672 1042h0M675 1050h0M688 1040h0M692 1095h0M695 1160h0M700 1165h0M703 1175h0M706 1040h0M708 1050h0M710 1075h0M715 1065h0M718 1075h0M721 1118h0M726 1025h0M731 1035h0M735 1045h0M740 1030h0M745 1025h0M750 1030h0M755 1022h0M770 1022h0M785 1022h0M800 1022h0M815 1022h0M830 1022h0M845 1022h0M860 1022h0M875 1022h0M890 1022h0M905 1022h0M920 1022h0M935 1022h0M950 1022h0M965 1022h0M980 1022h0M995 1022h0"/>
    <path fill="none" stroke="#3a6eb0" stroke-width="7" stroke-linecap="round" d="M205 1030h0M208 1022h0M212 1025h0M218 1030h0M220 1022h0M203 1083h0M215 1100h0M225 1133h0M230 1125h0M235 1148h0M238 1160h0M240 1140h0M245 1135h0M250 1125h0M255 1095h0M258 1120h0M262 1118h0M268 1098h0M270 1120h0M272 1135h0M275 1160h0M280 1155h0M285 1120h0M290 1135h0M295 1130h0M300 1160h0M305 1150h0M310 1155h0M315 1160h0M320 1158h0M325 1165h0M332 1165h0M338 1185h0M342 1185h0M348 1180h0M352 1178h0M358 1182h0M362 1185h0M366 1175h0M372 1180h0M378 1165h0M382 1160h0M386 1155h0M393 1148h0M398 1165h0M402 1160h0M405 1170h0M412 1168h0M416 1150h0M420 1160h0M424 1168h0M430 1165h0M434 1200h0M438 1195h0M446 1185h0M450 1170h0M455 1190h0M460 1148h0M463 1075h0M467 1048h0M471 1042h0M476 1045h0M480 1030h0M484 1058h0M490 1055h0M496 1185h0M500 1180h0M505 1170h0M510 1160h0M515 1158h0M520 1165h0M525 1170h0M530 1135h0M535 1125h0M540 1038h0M545 1035h0M550 1025h0M555 1022h0M560 1030h0M565 1032h0M570 1030h0M575 1020h0M590 1018h0M600 1018h0M610 1018h0M620 1018h0M630 1018h0M640 1018h0M650 1018h0M660 1018h0M670 1018h0M680 1018h0M690 1018h0M700 1018h0M710 1018h0M720 1018h0M730 1018h0M740 1018h0M750 1018h0M760 1018h0M770 1018h0M780 1018h0M790 1018h0M800 1018h0M810 1018h0M820 1018h0M830 1018h0M840 1018h0M850 1018h0M860 1018h0M870 1018h0M880 1018h0M890 1018h0M900 1018h0M910 1018h0M920 1018h0M930 1018h0M940 1018h0M950 1018h0M960 1018h0M970 1018h0M980 1018h0M990 1018h0M1000 1018h0M1010 1018h0M1020 1018h0M1025 1018h0"/>
    <path fill="none" stroke="#3a9a3a" stroke-width="7" stroke-linecap="round" d="M1000 1200h0M1005 1201h0M1010 1200h0"/>
    <text x="1132" y="1020" font-size="11" fill="#444" font-family="Georgia, serif">Names</text>
    <g>
      <circle cx="1114" cy="1017" r="3.5" fill="#8fb3d9"/>
      <circle cx="1114" cy="1036" r="3.5" fill="#f2b27a"/>
      <circle cx="1114" cy="1054" r="3.5" fill="#3a9a3a"/>
      <circle cx="1114" cy="1073" r="3.5" fill="#d86a6a"/>
      <circle cx="1114" cy="1091" r="3.5" fill="#b59ad8"/>
      <circle cx="1114" cy="1110" r="3.5" fill="#ad8f86"/>
      <circle cx="1114" cy="1128" r="3.5" fill="#e7a7d1"/>
      <circle cx="1114" cy="1147" r="3.5" fill="#b0b0b0"/>
      <circle cx="1114" cy="1165" r="3.5" fill="#b9b83a"/>
      <circle cx="1114" cy="1184" r="3.5" fill="#8fd6e2"/>
      <circle cx="1114" cy="1202" r="3.5" fill="#3a6eb0"/>
    </g>
  </svg>
</section>
</body>
</html>
```